FinTech company looking to revamp and expand client-facing interface for our financial models

Pellworth Engines currently has a very simple website that allows clients to interact with our financial models. We are looking to completely redesign the current site and add several extra pages to provide extra functionality. We want the design to have a modern, slick feel, that will work on both a desktop or a tablet. It should be straightforward for clients to move between different pages at any time, and clear from the layout how to interact with the more advanced features. We have included screenshots of existing pages in the attached design brief, as well as sketches of the functionality required by the new pages, but can't provide a direct link to the current site.
Target Market(s)
Professional investors that will be paying to access the interface
Industry/Entity Type
Finance
Number of Pages Required
4 page
Colors
Designer to choose colors to be used in the design.
Look and feel
Each slider illustrates characteristics of the customer's brand and the style your logo design should communicate.

```html
<!DOCTYPE html>
<html lang="en">
<head>
<meta charset="utf-8">
<title>Pellworth Engines – Models &amp; Factors</title>
<link href="https://fonts.googleapis.com/css2?family=Poppins:wght@400;500;600;700&family=Open+Sans:wght@400&display=swap" rel="stylesheet">
<style>
  :root{
    --bg:#104f47;
    --panel:#ffffff;
    --nav:#2a2a2a;
    --teal:#33b8a5;
    --teal-text:#2fb29f;
    --row-alt:#e7f4f1;
    --ink:#222222;
    --line:#d9dedd;
    --menu:#e6f4f1;
  }
  *{box-sizing:border-box;margin:0;padding:0}
  html,body{width:1080px;height:1200px;overflow:hidden}
  body{background:var(--bg);font-family:"Poppins",sans-serif;color:var(--ink);position:relative}
  .screen{position:absolute;left:120px;width:840px;background:var(--panel)}
  .screen--models{top:84px;height:509px}
  .screen--factors{top:657px;height:438px}
  .navbar{position:absolute;left:0;right:0;height:45px;background:var(--nav);color:#fff;font-weight:700;font-size:11px}
  .screen--models .navbar{top:22px}
  .screen--factors .navbar{top:18px}
  .navbar span,.navbar a{position:absolute;top:0;height:45px;line-height:45px;color:#fff;text-decoration:none;white-space:nowrap}
  .nav-tab--active{background:var(--teal);text-align:center}
  .brand{left:0;right:0;text-align:center;font-size:12px;font-weight:600;letter-spacing:.2px}
  .nav-link svg{width:9px;height:9px;vertical-align:-1px;margin-right:3px;fill:#fff}
  .nav-link--open{background:var(--menu);color:var(--teal-text)!important;text-align:center}
  .nav-link--open svg{fill:var(--teal-text)}
  .sep{font-weight:400}
  .dropdown{position:absolute;left:538px;top:67px;width:115px;background:var(--menu);border:1px solid #d6e9e5;font-size:10px;font-weight:500;color:var(--teal-text)}
  .dropdown li{list-style:none;height:24px;line-height:24px;padding-left:22px}
  .dropdown li:first-child{background:#fff;height:29px;line-height:27px;border-bottom:1px solid #d6e9e5}
  .field-label{position:absolute;color:var(--teal-text);font-weight:600;font-size:10.5px;line-height:13px;white-space:nowrap}
  .field{position:absolute;height:29px;width:137px;border:1px solid #d4d4d4;box-shadow:0 1px 2px rgba(0,0,0,.12);color:var(--teal-text);font-weight:600;font-size:10.5px;line-height:27px;padding-left:13px}
  .export{position:absolute;left:20px;color:var(--teal-text);font-weight:600;font-size:10.5px}
  .export svg{width:9px;height:9px;fill:var(--teal-text);vertical-align:-1px;margin-right:3px}
  table{position:absolute;left:21px;width:797px;border-collapse:collapse;table-layout:fixed}
  th{background:var(--teal);color:#fff;font-weight:600;font-size:10.5px;text-align:left;padding-left:6px;border-right:1px solid #5cc7b8}
  td{font-size:10.5px;padding-left:6px;border-right:1px solid var(--line);line-height:12px}
  td:first-child,td.sector{font-weight:500}
  tbody tr:nth-child(even){background:var(--row-alt)}
  .models-table{top:200px}
  .models-table th{height:44px}
  .models-table td{height:44.4px}
  .factors-table{top:137px}
  .factors-table th{height:42px}
  .factors-table td{height:44.4px}
  .footer{position:absolute;left:0;right:0;text-align:center;font-family:"Open Sans",sans-serif;font-size:11.5px;color:#333}
  .footer-rule{position:absolute;left:0;right:0;height:1px;background:#e1e1e1}
</style>
</head>
<body>

<section class="screen screen--models">
  <nav class="navbar">
    <span style="left:21px">QVANTA</span>
    <span class="nav-tab--active" style="left:78px;width:56px">250D</span>
    <span style="left:154px">83D</span>
    <span style="left:203px">42D</span>
    <span class="brand">PELLWORTH ENGINES</span>
    <a class="nav-link nav-link--open" style="left:538px;width:85px"><svg viewBox="0 0 10 10"><path d="M5 1L0 5.5h1.5V9h2.5V6.5h2V9h2.5V5.5H10z"/></svg>MODELS</a>
    <a class="nav-link" style="left:626px"><svg viewBox="0 0 10 10"><circle cx="5" cy="5" r="3.2" fill="none" stroke="#fff" stroke-width="1.4" stroke-dasharray="1.6 .9"/><circle cx="5" cy="5" r="1.2" fill="none" stroke="#fff" stroke-width=".9"/></svg>SENSITIVITIES</a>
    <span class="sep" style="left:726px">|</span>
    <a class="nav-link" style="left:745px"><svg viewBox="0 0 10 10"><path d="M5 .5l1.4 3 3.2.3-2.4 2.1.7 3.2L5 7.5 2.1 9.1l.7-3.2L.4 3.8l3.2-.3z"/></svg>FAVORITES</a>
  </nav>
  <ul class="dropdown">
    <li>» EQUITIES</li><li>» ETFS</li><li>» PAIRS</li><li>» ETF PAIRS</li><li>» FACTORS</li>
  </ul>

  <div class="field-label" style="left:20px;top:88px">QUALITY&nbsp;&nbsp; THRESHOLD :</div>
  <div class="field" style="left:148px;top:80px">-10</div>
  <div class="field-label" style="left:301px;top:81px">ABS. stat<br>THERSHOLD :</div>
  <div class="field" style="left:375px;top:80px">-10</div>
  <div class="export" style="top:131px"><svg viewBox="0 0 10 10"><path d="M0 1h5v1.5H1.5v5H5V9H0zM5 3.5V2l4 3-4 3V6.5H3v-3z"/></svg>EXPORT</div>

  <table class="models-table">
    <colgroup><col style="width:60px"><col style="width:100px"><col style="width:78px"><col style="width:54px"><col style="width:72px"><col style="width:54px"><col style="width:74px"><col style="width:54px"><col style="width:54px"><col style="width:72px"><col style="width:71px"><col style="width:54px"></colgroup>
    <thead><tr><th>ID</th><th>SECTOR</th><th>TIME</th><th>QUALITY</th><th>STAT 1</th><th>STAT 2</th><th>STAT 3</th><th>STAT 4</th><th>STAT 5</th><th>STAT 6</th><th>STAT 7</th><th>STAT 8</th></tr></thead>
    <tbody>
      <tr><td>Model 1</td><td class="sector">Materials</td><td>2019-07-03<br>12:15:00.000</td><td>30.2288</td><td>2.01574</td><td>23.305</td><td>-0.149368</td><td>22.3054</td><td>4.63714</td><td>0.945706</td><td>2.81949</td><td>2.60858</td></tr>
      <tr><td>Model 2</td><td class="sector">Industrials</td><td>2019-07-03<br>12:15:00.000</td><td>32.8694</td><td>0.87307</td><td>32.185</td><td>-0.0336927</td><td>33.9911</td><td>11.5693</td><td>-0.472968</td><td>-0.830458</td><td>6.80646</td></tr>
      <tr><td>Model 3</td><td class="sector">Consumer Discretionary</td><td>2019-07-03<br>12:15:00.000</td><td>1.66002</td><td>-0.569222</td><td>159.814</td><td>0.0252328</td><td>172.616</td><td>10.2875</td><td>-0.750396</td><td>-0.385309</td><td>4.69146</td></tr>
      <tr><td>Model 4</td><td class="sector">Information Technology</td><td>2019-07-03<br>12:15:00.000</td><td>45.6856</td><td>0.412148</td><td>202.488</td><td>0.00849232</td><td>205.834</td><td>11.9094</td><td>-0.137913</td><td>0.449595</td><td>3.85106</td></tr>
      <tr><td>Model 5</td><td class="sector">Information Technology</td><td>2019-07-03<br>12:15:00.000</td><td>75.7733</td><td>7.06728</td><td>188.605</td><td>0.016913</td><td>181.665</td><td>3.82241</td><td>0.981019</td><td>1.29847</td><td>3.34927</td></tr>
    </tbody>
  </table>
  <div class="footer-rule" style="top:466px"></div>
  <div class="footer" style="top:476px">© Copyrights 2019 Pellworth Engines | All Rights Reserved</div>
</section>

<section class="screen screen--factors">
  <nav class="navbar">
    <span style="left:21px">FACTORS</span>
    <span class="nav-tab--active" style="left:90px;width:56px">250D</span>
    <span style="left:167px">83D</span>
    <span style="left:216px">42D</span>
    <span class="brand">PELLWORTH ENGINES</span>
    <a class="nav-link" style="left:542px"><svg viewBox="0 0 10 10"><path d="M5 1L0 5.5h1.5V9h2.5V6.5h2V9h2.5V5.5H10z"/></svg>MODELS</a>
    <span class="sep" style="left:614px">|</span>
    <a class="nav-link" style="left:626px"><svg viewBox="0 0 10 10"><circle cx="5" cy="5" r="3.2" fill="none" stroke="#fff" stroke-width="1.4" stroke-dasharray="1.6 .9"/><circle cx="5" cy="5" r="1.2" fill="none" stroke="#fff" stroke-width=".9"/></svg>SENSITIVITIES</a>
    <span class="sep" style="left:728px">|</span>
    <a class="nav-link" style="left:747px"><svg viewBox="0 0 10 10"><path d="M5 .5l1.4 3 3.2.3-2.4 2.1.7 3.2L5 7.5 2.1 9.1l.7-3.2L.4 3.8l3.2-.3z"/></svg>FAVORITES</a>
  </nav>

  <div class="field-label" style="left:20px;top:84px">STAR 1 THRESHOLD :</div>
  <div class="field" style="left:135px;top:76px">-10</div>
  <div class="field-label" style="left:293px;top:84px">STAR 1 THRESHOLD :</div>
  <div class="field" style="left:408px;top:76px">-10</div>
  <div class="field-label" style="left:565px;top:84px">STAR 1 THRESHOLD :</div>
  <div class="field" style="left:681px;top:76px">-10</div>
  <div class="export" style="top:113px"><svg viewBox="0 0 10 10"><path d="M0 1h5v1.5H1.5v5H5V9H0zM5 3.5V2l4 3-4 3V6.5H3v-3z"/></svg>EXPORT</div>

  <table class="factors-table">
    <colgroup><col style="width:84px"><col style="width:100px"><col style="width:97px"><col style="width:86px"><col style="width:86px"><col style="width:86px"><col style="width:86px"><col style="width:86px"><col style="width:86px"></colgroup>
    <thead><tr><th>FACTOR</th><th>ID</th><th>SECTOR</th><th>STAT 1</th><th>STAT 2</th><th>STAT 3</th><th>STAT 4</th><th>STAT 5</th><th>STAT 6</th></tr></thead>
    <tbody>
      <tr><td>Factor 1</td><td class="sector">Model 1</td><td class="sector">Materials</td><td>-1.4</td><td>0.1</td><td>-3.1</td><td>0.7</td><td>30.2</td><td>0.9</td></tr>
      <tr><td>Factor 2</td><td class="sector">Model 1</td><td class="sector">Materials</td><td>2.8</td><td>0.1</td><td>6.1</td><td>100</td><td>30.2</td><td>0.9</td></tr>
      <tr><td>Factor 3</td><td class="sector">Model 1</td><td class="sector">Materials</td><td>-3.7</td><td>2.7</td><td>-7.2</td><td>100</td><td>30.2</td><td>0.9</td></tr>
      <tr><td>Factor 1</td><td class="sector">Model 2</td><td class="sector">Industrials</td><td>2.8</td><td>0.2</td><td>2.7</td><td>0.5</td><td>32.9</td><td>-0.5</td></tr>
      <tr><td>Factor 2</td><td class="sector">Model 2</td><td class="sector">industrials</td><td>0.8</td><td>0.3</td><td>2.5</td><td>0.5</td><td>32.9</td><td>-0.5</td></tr>
    </tbody>
  </table>
  <div class="footer-rule" style="top:401px"></div>
  <div class="footer" style="top:411px">© Copyrights 2019 Pellworth Engines | All Rights Reserved</div>
</section>

</body>
</html>
```